Business Card Design Project

Business card based on attached logo

Todd Merrick
Todd@lorvantest.com
877-514-9073 ext. 318
Www.LorvanTest.com

Industry/Entity Type

Business

```html
<!DOCTYPE html>
<html lang="en">
<head>
<meta charset="utf-8">
<title>LorvanTest Business Card Set</title>
<link href="https://fonts.googleapis.com/css2?family=Source+Sans+3:wght@400;600;700&display=swap" rel="stylesheet">
<style>
  :root {
    --backdrop: #e9e4de;
    --card-white: #ffffff;
    --ink: #1a1a1a;
    --ink-soft: #3a3a3a;
    --grey-text: #444444;
    --brand-red: #e0242b;
    --deep-red: #8e1b1f;
    --red-top: #c8262c;
    --red-bottom: #9f1b20;
    --pearl-top: #f6f6f6;
    --pearl-bottom: #e3e3e3;
    --label: #222222;
  }
  * { box-sizing: border-box; margin: 0; padding: 0; }
  html, body { width: 1200px; height: 788px; overflow: hidden; }
  body {
    position: relative;
    background: var(--backdrop);
    font-family: "Source Sans 3", "Helvetica Neue", Arial, sans-serif;
    color: var(--ink);
  }
  .side-label {
    position: absolute;
    width: 526px;
    text-align: center;
    font-size: 22px;
    color: var(--label);
  }
  .card {
    position: absolute;
    width: 526px;
    height: 301px;
    border-radius: 20px;
    overflow: hidden;
    background: var(--card-white);
  }
  .card--left { left: 53px; }
  .card--right { left: 622px; }
  .card--top { top: 73px; }
  .card--bottom { top: 445px; }
  .card--red { background: linear-gradient(180deg, var(--red-top), var(--red-bottom)); }
  .card--pearl { background: linear-gradient(180deg, var(--pearl-top), var(--pearl-bottom)); }

  .corner-swoosh { position: absolute; left: 0; top: 0; }

  .wordmark {
    position: absolute;
    left: 0; right: 0;
    text-align: center;
    font-weight: 700;
    color: var(--ink);
    letter-spacing: -0.5px;
    line-height: 1;
  }
  .wordmark__dot {
    display: inline-block;
    background: var(--brand-red);
    vertical-align: top;
  }
  .wordmark--front { top: 112px; font-size: 54px; }
  .wordmark--front .wordmark__dot { width: 16px; height: 16px; margin-left: 6px; }
  .wordmark--large { top: 112px; font-size: 66px; }
  .wordmark--large .wordmark__dot { width: 20px; height: 20px; margin-left: 8px; }
  .wordmark--light { color: var(--card-white); }
  .wordmark--light .wordmark__dot { background: var(--card-white); }

  .holder-name {
    position: absolute;
    top: 185px; left: 0; right: 0;
    text-align: center;
    font-size: 18px;
    font-weight: 700;
    color: var(--deep-red);
  }
  .contact-line {
    position: absolute;
    left: 0; right: 0;
    text-align: center;
    font-size: 13px;
    color: var(--ink-soft);
  }
  .contact-line--phone { top: 217px; }
  .contact-line--web { top: 243px; }
  .contact-line b { color: var(--brand-red); font-weight: 700; }
  .contact-line .divider { margin: 0 6px; color: var(--ink); font-weight: 700; }

  .web-address {
    position: absolute;
    top: 249px; left: 0; right: 0;
    text-align: center;
    font-size: 18px;
    color: var(--grey-text);
  }
  .web-address--light { color: var(--card-white); }

  .raised-panel {
    position: absolute;
    left: 81px; top: 82px;
    width: 360px; height: 125px;
    background: linear-gradient(180deg, #ffffff, #f1f1f1);
    border: 1px solid #dcdcdc;
    box-shadow: 0 10px 12px -6px rgba(0,0,0,0.35);
  }
  .raised-panel .wordmark { top: 40px; font-size: 44px; }
  .raised-panel .wordmark__dot { width: 13px; height: 13px; margin-left: 5px; }
</style>
</head>
<body>

  <div class="side-label" style="left:53px; top:34px;">Front</div>
  <div class="side-label" style="left:622px; top:34px;">Back - 1</div>
  <div class="side-label" style="left:53px; top:405px;">Back - 2</div>
  <div class="side-label" style="left:622px; top:405px;">Back - 3</div>

  <section class="card card--left card--top">
    <svg class="corner-swoosh" width="526" height="301" viewBox="0 0 526 301" aria-hidden="true">
      <path d="M455 0 Q505 10 526 70 L526 0 Z" fill="var(--brand-red)"/>
      <path d="M455 0 Q505 10 526 70" fill="none" stroke="#111" stroke-width="3" transform="translate(-8 3)"/>
      <path d="M0 230 Q12 285 78 301 L0 301 Z" fill="var(--brand-red)"/>
      <path d="M0 230 Q12 285 78 301" fill="none" stroke="#111" stroke-width="3" transform="translate(4 -6)"/>
    </svg>
    <div class="wordmark wordmark--front">LorvanTest<span class="wordmark__dot"></span></div>
    <div class="holder-name">Todd Merrick</div>
    <div class="contact-line contact-line--phone"><b>phone</b> 877-514-9073 ext. 318</div>
    <div class="contact-line contact-line--web"><b>email</b> Todd@lorvantest.com<span class="divider">|</span><b>web</b> www.LorvanTest.com</div>
  </section>

  <section class="card card--right card--top">
    <div class="wordmark wordmark--large">LorvanTest<span class="wordmark__dot"></span></div>
    <div class="web-address">www.LorvanTest.com</div>
  </section>

  <section class="card card--left card--bottom card--red">
    <div class="wordmark wordmark--large wordmark--light">LorvanTest<span class="wordmark__dot"></span></div>
    <div class="web-address web-address--light">www.LorvanTest.com</div>
  </section>

  <section class="card card--right card--bottom card--pearl">
    <div class="raised-panel">
      <div class="wordmark">LorvanTest<span class="wordmark__dot"></span></div>
    </div>
    <div class="web-address">www.LorvanTest.com</div>
  </section>

</body>
</html>
```